Corvane Business Cards

Front of business card will have logo, name, address, & telephone number. Back of card will have a list of services provided - Roads, Substation Pads, Temporary Pads, Site Pads, Land Leveling, Powerline Row Cleaning, Land Clearing, Gates, Fencing, Construction Entrances, Excavation, Trenching, Underground Utilities, Directional Boring, Pile Driving. We are a construction company that uses heavy equipment like bulldozers, motor graders/blades, dump trucks, backhoes, hydro axes, & skid loaders. We build roads, pads, & install electric utility lines & waterlines underground. This logo is new. The word "Construction" can be smaller as uploaded 2 example edited logos. We will be using this card design for many employees.
Target Market(s)
Industrial Electric Powerline, Wind Turbine, Solar Panel, & Water Utility companies.
Contact Information for Business Card
Name/Position - Dwayne Halster - Owner
Address: 4875 FM 309
Caldrow, NX 79412
Phone number - (325) 482-5096

```html
<!DOCTYPE html>
<html lang="en">
<head>
<meta charset="utf-8">
<title>Corvane Construction – Business Cards</title>
<link href="https://fonts.googleapis.com/css2?family=Poppins:wght@400;500;600;700&display=swap" rel="stylesheet">
<style>
  :root {
    --maroon: #3a0e19;
    --maroon-deep: #310b14;
    --card-light: #e6e6e8;
    --text-grey: #4a4446;
    --backdrop: #a6a6a7;
    --white: #ffffff;
  }
  * { box-sizing: border-box; margin: 0; padding: 0; }
  html, body {
    width: 1105px; height: 1200px; overflow: hidden;
    background: var(--backdrop);
    font-family: "Poppins", sans-serif;
  }
  .sheet { position: relative; width: 1105px; height: 1200px; }
  .card { position: absolute; left: 182px; width: 746px; }
  .card--front { top: 119px; height: 427px; background: var(--card-light); color: var(--maroon); }
  .card--back { top: 637px; height: 425px; background: var(--maroon-deep); color: var(--white); }

  /* front */
  .brand { position: absolute; left: 36px; top: 78px; color: var(--maroon); }
  .brand__name { display: block; font-size: 50px; font-weight: 600; line-height: 1; letter-spacing: 1px; }
  .brand__sub { display: block; font-size: 23px; font-weight: 500; line-height: 1; margin-top: 32px; }

  .person { position: absolute; right: 41px; top: 241px; text-align: right; }
  .person__name { font-size: 22px; font-weight: 600; letter-spacing: 0.3px; line-height: 1.15; }
  .person__role { font-size: 16px; color: var(--maroon); line-height: 1.3; }

  .rule { position: absolute; left: 36px; right: 41px; top: 302px; height: 1px; background: var(--maroon); }

  .address { position: absolute; left: 36px; top: 313px; font-size: 17px; line-height: 22px; color: var(--text-grey); font-style: normal; }
  .contact { position: absolute; right: 41px; top: 313px; font-size: 17px; line-height: 22px; color: var(--text-grey); }
  .contact__row { display: flex; justify-content: flex-end; align-items: center; gap: 8px; }
  .contact__icon { width: 12px; height: 12px; fill: var(--maroon); }

  .band {
    position: absolute; left: 0; right: 0; top: 381px; height: 28px;
    background: var(--maroon); color: var(--white);
    display: flex; justify-content: space-between; align-items: center;
    padding: 0 41px 0 36px; font-size: 17px;
  }
  .band__mark { font-size: 12px; font-weight: 600; letter-spacing: 0.3px; }

  /* back */
  .back-brand {
    position: absolute; left: 0; right: 0; top: 152px; text-align: center;
    font-size: 78px; font-weight: 600; line-height: 1; letter-spacing: 2px;
  }
  .services {
    position: absolute; left: 0; right: 0; top: 339px; text-align: center;
    font-size: 17px; line-height: 20px;
  }
</style>
</head>
<body>
<main class="sheet">
  <section class="card card--front" aria-label="Business card front">
    <div class="brand">
      <span class="brand__name">CORVANE</span>
      <span class="brand__sub">CONSTRUCTION</span>
    </div>
    <div class="person">
      <p class="person__name">DWAYNE HALSTER</p>
      <p class="person__role">Owner</p>
    </div>
    <div class="rule"></div>
    <address class="address">4875 FM 309<br>Caldrow, NX 79412</address>
    <div class="contact">
      <div class="contact__row">(325) 482-5096
        <svg class="contact__icon" viewBox="0 0 24 24" aria-hidden="true"><path d="M6.6 10.8a15.1 15.1 0 0 0 6.6 6.6l2.2-2.2a1 1 0 0 1 1-.25 11.4 11.4 0 0 0 3.6.57 1 1 0 0 1 1 1V20a1 1 0 0 1-1 1A17 17 0 0 1 3 4a1 1 0 0 1 1-1h3.5a1 1 0 0 1 1 1c0 1.25.2 2.45.57 3.57a1 1 0 0 1-.25 1z"/></svg>
      </div>
      <div class="contact__row">info@corvaneconstruction.com
        <svg class="contact__icon" viewBox="0 0 24 24" aria-hidden="true"><path d="M2 5h20v14H2z"/><path d="M3 6l9 7 9-7" fill="none" stroke="var(--card-light)" stroke-width="1.8"/></svg>
      </div>
    </div>
    <div class="band">
      <span>www.corvaneconstruction.com</span>
      <span class="band__mark">CORVANE</span>
    </div>
  </section>

  <section class="card card--back" aria-label="Business card back">
    <div class="back-brand">CORVANE</div>
    <p class="services">
      Roads • Substation Pads•Temporary Pads • Site Pads • Land Leveling<br>
      Powerline Row Cleaning • Land Clearing • Gates• Fencing • Construction Entrances<br>
      Excavation • Trenching • Underground Utilities• Directional Boring • Pile Driving
    </p>
  </section>
</main>
</body>
</html>
```